Postcard for our major fundraising event - KindlingJOY2018

Bright Harbor KIDS Camp (BHK) and Youth Summit Trail Camp (YSTC) are ministries of Lindell Fellowship Church that serve Ventura County children of abuse, abandonment and neglect living in foster care. We are looking for a postcard design to promote our single largest fundraising event of the year, GatheringJOY2018, to raise awareness and support for children of abuse. GatheringJOY is a dinner banquet on at an exclusive outdoor venue, "Willow Hollow" with a rustic, ranch feel and with spectacular panoramic views of the City of Camarillo. The event will include music, refreshments, appetizers, a Santa Maria-style barbeque (BBQ), coffee and dessert, testimonials from camp, prize drawings, an opportunity to partner with BHK and YSTC, and time to socialize before and after.
Updates

I have just uploaded text copy to help designers come closer to what we are looking for. Thank you very much for your interest! -Rob

Target Market(s)

People from both within and from outside our sponsoring church who have a heart for hurting children and who are willing and able to financially support our camping (BHK & YSTC) ministries.

Industry/Entity Type

Church

Font styles to use
Serif
Decorative
Script

Requirements
Must have
• Name: GatheringJOY2018... raising awareness and support for children of abuse
• Date: Thursday, May 24, 2018, 6:30-8:00 pm
• Place: Willow Hollow at Dunmore Ranch, 2715 Barlow Lane, Somis, California.
• Cost: $30 per person
• Tickets: Available at Tixlane.com
• Front side should include the elements of the event (although not necessarily bulleted like below):
• • Social hour
• • Music
• • Hors d’eourves
• • Refreshments
• • Santa Maria-style BBQ dinner
• • Coffee & dessert
• • Prize drawings
• • Stories from camp
• See attachment for suggested copy for back side.
• BHK and YSTC logos should be included on the postcard. I’ve uploaded a variety of photos for the designer to choose from; they do not necessarily all have to be included. There are also lots more pics available on our Facebook (Bright Harbor KIDS of Ventura).
• The front-side of the postcard can be entirely images and text. The back-side of the post card should include our return address at the top left ("BHK/YSTC of Lindell Fellowship Church, 418 Kestrel Ridge Way, Ventura, CA 93017") and should leave at least the right half of the postcard clear for addressing and postage.
• BHK colors are purple (Pantone 267) and red (Pantone 186). YSTC colors are green and yellow.
Nice to have
• A selection of camp photos large enough to easily view, but no so many that they are too small to identify. And, perhaps, a design element that evokes a rustic, outdoors, western, ranch feel, but not so much that it seems that we are promoting a country hoedown.
Should not have
• Anything sexual or sensual, related to alcoholic beverages, gambling, guns, or anything negative.

```html
<!DOCTYPE html>
<html lang="en">
<head>
<meta charset="utf-8">
<title>GatheringJOY 2018 Postcard</title>
<link href="https://fonts.googleapis.com/css2?family=Montserrat:ital,wght@0,400;0,500;0,600;0,700;1,400;1,500&family=Dancing+Script:wght@500&display=swap" rel="stylesheet">
<style>
  :root {
    --purple: #3f2a82;
    --purple-deep: #33216e;
    --red: #d21f2b;
    --white: #ffffff;
    --ink: #2b2358;
    --grey: #6b6b6b;
    --stamp: #e3e3e3;
    --ground: #e9e9ec;
    --leaf-light: #8fbf5a;
    --leaf-dark: #2f5a22;
    --ystc-green: #2f9a48;
  }
  * { box-sizing: border-box; margin: 0; padding: 0; }
  html, body { width: 1200px; height: 903px; overflow: hidden; background: var(--ground); }
  body { font-family: "Montserrat", sans-serif; color: var(--ink); }

  .sheet { position: relative; width: 1200px; height: 903px; }

  .card {
    position: absolute; left: 280px; width: 640px; height: 427px;
    background: var(--white); overflow: hidden;
    box-shadow: 0 4px 14px rgba(0,0,0,.18);
  }
  .card--front { top: 14px; }
  .card--back { top: 462px; }

  .card__art { position: absolute; inset: 0; }

  /* front */
  .features { position: absolute; left: 44px; top: 56px; list-style: none; }
  .features li {
    display: flex; align-items: center; gap: 12px;
    color: var(--white); font-size: 17px; letter-spacing: .6px; height: 33px;
  }
  .features svg { flex: none; }

  /* back */
  .back-left { position: absolute; left: 0; top: 0; width: 330px; height: 427px; }
  .logos { position: absolute; top: 16px; left: 26px; right: 16px; display: flex; justify-content: space-between; align-items: center; }
  .logo { display: flex; align-items: center; gap: 6px; font-weight: 700; font-size: 13px; }
  .logo--bhk { color: var(--purple); }
  .logo--ystc { color: var(--ystc-green); }
  .logo__square { width: 14px; height: 14px; background: var(--red); }
  .logo__circle { width: 30px; height: 30px; border-radius: 50%; background: var(--ystc-green); }

  .hosts { position: absolute; top: 56px; left: 20px; right: 14px; text-align: center; font-size: 8.6px; line-height: 1.3; font-weight: 500; }
  .hosts em { font-weight: 600; }

  .banner {
    position: absolute; top: 92px; left: 0; width: 330px; height: 36px;
    background: var(--red); color: var(--white);
    font-size: 25px; font-weight: 700; letter-spacing: .5px;
    display: flex; align-items: center; justify-content: center;
  }
  .tagline { position: absolute; top: 130px; left: 0; width: 330px; text-align: center; font-family: "Dancing Script", cursive; font-size: 14px; color: var(--ink); }
  .venue { position: absolute; top: 152px; left: 0; width: 330px; text-align: center; line-height: 1.25; }
  .venue__lead { color: var(--red); font-style: italic; font-size: 10.5px; }
  .venue__name { color: var(--purple); font-size: 15px; font-weight: 500; }
  .date-pill {
    display: inline-block; margin-top: 3px; padding: 1px 12px;
    background: var(--red); color: var(--white); border-radius: 4px;
    font-size: 16px; font-weight: 500;
  }
  .time { color: var(--ink); font-size: 15px; font-weight: 500; margin-top: 2px; }

  .tickets { position: absolute; top: 262px; left: 22px; right: 14px; display: flex; align-items: center; gap: 10px; }
  .tickets__box { border: 1.5px solid #bdbdbd; border-radius: 5px; padding: 2px 8px; position: relative; }
  .tickets__label { position: absolute; top: -9px; left: 36px; background: var(--white); padding: 0 4px; color: var(--red); font-size: 10px; font-weight: 700; }
  .tickets__price { color: var(--purple); font-size: 20px; font-weight: 500; }
  .tickets__price b { color: var(--red); font-weight: 700; }
  .tickets__where { font-size: 11px; line-height: 1.2; color: var(--ink); font-weight: 500; }
  .tickets__where span { color: var(--red); font-size: 13px; display: block; }

  .benefit { position: absolute; top: 306px; left: 10px; right: 8px; text-align: center; font-size: 10px; line-height: 1.3; font-weight: 500; }
  .benefit span { color: var(--red); font-weight: 600; }

  .info { position: absolute; left: 0; bottom: 0; width: 330px; height: 82px; background: var(--purple); color: var(--white); font-size: 9px; line-height: 1.35; }
  .info__title { position: absolute; top: 6px; left: 0; width: 100%; text-align: center; font-weight: 600; font-size: 9.5px; }
  .contact { position: absolute; top: 22px; }
  .contact--bhk { left: 14px; }
  .contact--ystc { left: 170px; }
  .contact__org { color: #ff6b73; font-weight: 600; }
  .contact__name { font-weight: 600; }
  .contact__row { display: flex; align-items: center; gap: 4px; }

  .divider { position: absolute; left: 340px; top: 22px; width: 2px; height: 380px; background: var(--purple); }
  .return-address { position: absolute; left: 360px; top: 40px; font-size: 10px; line-height: 1.3; color: var(--grey); font-weight: 500; }
  .stamp { position: absolute; right: 26px; top: 34px; width: 62px; height: 68px; background: var(--stamp); }
  .address-lines { position: absolute; left: 382px; right: 38px; top: 230px; }
  .address-lines div { height: 38px; border-bottom: 1px solid #b5b5b5; }
</style>
</head>
<body>
<main class="sheet">

  <section class="card card--front" aria-label="Postcard front">
    <svg class="card__art" width="640" height="427" viewBox="0 0 640 427">
      <defs>
        <linearGradient id="canopy" x1="0" y1="0" x2="1" y2="1">
          <stop offset="0" stop-color="var(--leaf-light)"/>
          <stop offset=".6" stop-color="#4f8a34"/>
          <stop offset="1" stop-color="var(--leaf-dark)"/>
        </linearGradient>
      </defs>
      <rect width="640" height="427" fill="url(#canopy)" role="img" aria-label="Photo: campers in helmets and harnesses on a ropes course among green trees"/>
      <path d="M0,0 L215,0 Q300,150 410,362 L0,362 Z" fill="var(--purple)"/>
      <path d="M0,362 L410,362 L420,370 L0,370 Z" fill="var(--white)"/>
      <path d="M0,370 L420,370 L455,427 L0,427 Z" fill="var(--red)"/>
      <path d="M0,384 L428,384 L432,390 L0,390 Z" fill="var(--purple-deep)" opacity=".35"/>
    </svg>
    <ul class="features">
      <li><svg width="14" height="14" viewBox="0 0 14 14"><circle cx="7" cy="7" r="6" fill="none" stroke="var(--red)" stroke-width="1.6"/><path d="M4 7.2 L6.3 9.3 L10.5 4.6" fill="none" stroke="var(--red)" stroke-width="1.6"/></svg>Social hour</li>
      <li><svg width="14" height="14" viewBox="0 0 14 14"><circle cx="7" cy="7" r="6" fill="none" stroke="var(--red)" stroke-width="1.6"/><path d="M4 7.2 L6.3 9.3 L10.5 4.6" fill="none" stroke="var(--red)" stroke-width="1.6"/></svg>Music</li>
      <li><svg width="14" height="14" viewBox="0 0 14 14"><circle cx="7" cy="7" r="6" fill="none" stroke="var(--red)" stroke-width="1.6"/><path d="M4 7.2 L6.3 9.3 L10.5 4.6" fill="none" stroke="var(--red)" stroke-width="1.6"/></svg>Hors d’eourves</li>
      <li><svg width="14" height="14" viewBox="0 0 14 14"><circle cx="7" cy="7" r="6" fill="none" stroke="var(--red)" stroke-width="1.6"/><path d="M4 7.2 L6.3 9.3 L10.5 4.6" fill="none" stroke="var(--red)" stroke-width="1.6"/></svg>Refreshments</li>
      <li><svg width="14" height="14" viewBox="0 0 14 14"><circle cx="7" cy="7" r="6" fill="none" stroke="var(--red)" stroke-width="1.6"/><path d="M4 7.2 L6.3 9.3 L10.5 4.6" fill="none" stroke="var(--red)" stroke-width="1.6"/></svg>Coffee &amp; dessert</li>
      <li><svg width="14" height="14" viewBox="0 0 14 14"><circle cx="7" cy="7" r="6" fill="none" stroke="var(--red)" stroke-width="1.6"/><path d="M4 7.2 L6.3 9.3 L10.5 4.6" fill="none" stroke="var(--red)" stroke-width="1.6"/></svg>Santa Maria-style BBQ dinner</li>
      <li><svg width="14" height="14" viewBox="0 0 14 14"><circle cx="7" cy="7" r="6" fill="none" stroke="var(--red)" stroke-width="1.6"/><path d="M4 7.2 L6.3 9.3 L10.5 4.6" fill="none" stroke="var(--red)" stroke-width="1.6"/></svg>Prize drawings</li>
      <li><svg width="14" height="14" viewBox="0 0 14 14"><circle cx="7" cy="7" r="6" fill="none" stroke="var(--red)" stroke-width="1.6"/><path d="M4 7.2 L6.3 9.3 L10.5 4.6" fill="none" stroke="var(--red)" stroke-width="1.6"/></svg>Stories from camp</li>
    </ul>
  </section>

  <section class="card card--back" aria-label="Postcard back">
    <div class="back-left">
      <div class="logos">
        <div class="logo logo--bhk"><span class="logo__square"></span>Bright Harbor KIDS</div>
        <div class="logo logo--ystc"><span class="logo__circle"></span>YSTC</div>
      </div>
      <p class="hosts">Bright Harbor KIDS Camp &amp; Youth Summit Trail Camp<br>of Lindell Fellowship Church<br><em>invite you to join us for</em></p>
      <div class="banner">GatheringJOY 2018</div>
      <p class="tagline">raising awareness and support for children of abuse</p>
      <div class="venue">
        <div class="venue__lead">at the exclusive</div>
        <div class="venue__name">Willow Hollow at Dunmore Ranch</div>
        <div class="venue__name">2715 Barlow Lane, Somis, CA</div>
        <div class="date-pill">Thursday, May 24, 2018</div>
        <div class="time">6:30-8:00 pm</div>
      </div>
      <div class="tickets">
        <div class="tickets__box">
          <span class="tickets__label">TICKETS:</span>
          <span class="tickets__price"><b>$30</b> per person</span>
        </div>
        <div class="tickets__where">Available at<span>Tixlane.com</span></div>
      </div>
      <p class="benefit">All proceeds to benefit<br><span>BHKC &amp; YSTC serving children of abuse ages 7-14.</span></p>
      <div class="info">
        <div class="info__title">For more information:</div>
        <div class="contact contact--bhk">
          <div class="contact__org">BHKC:</div>
          <div class="contact__name">Rob Halvers (Director)</div>
          <div class="contact__row"><svg width="8" height="8" viewBox="0 0 10 10"><path d="M2 1 L4 1 L5 3.5 L3.7 4.5 Q4.8 6.3 5.6 6.4 L6.6 5 L9 6 L9 8 Q5 9.5 1 2.5 Z" fill="var(--red)"/></svg>(805) 555-0142</div>
          <div class="contact__row"><svg width="8" height="7" viewBox="0 0 10 8"><rect width="10" height="8" rx="1" fill="var(--red)"/></svg>bhkventura@mailbox.net</div>
        </div>
        <div class="contact contact--ystc">
          <div class="contact__org">YSTC:</div>
          <div class="contact__name">Dean Sorvik (Director)</div>
          <div class="contact__row"><svg width="8" height="8" viewBox="0 0 10 10"><path d="M2 1 L4 1 L5 3.5 L3.7 4.5 Q4.8 6.3 5.6 6.4 L6.6 5 L9 6 L9 8 Q5 9.5 1 2.5 Z" fill="var(--red)"/></svg>(805) 555-0178</div>
          <div class="contact__row"><svg width="8" height="7" viewBox="0 0 10 8"><rect width="10" height="8" rx="1" fill="var(--red)"/></svg>deansorvikphoto@mailbox.net</div>
        </div>
      </div>
    </div>

    <div class="divider"></div>
    <p class="return-address">BHK/YSTC of<br>Lindell Fellowship Church,<br>418 Kestrel Ridge Way,<br>Ventura, CA 93017</p>
    <div class="stamp"></div>
    <div class="address-lines"><div></div><div></div><div></div></div>
  </section>

</main>
</body>
</html>
```